Harbor Ridge Painting Epoxy Flyer

We need a promotional flyer for a new epoxy floor coatings division of our painting company. We do epoxy garage floor coatings and paver sealing. It needs to be based on and very similar to the attached flyer. The garage floor picture needs to look more realistic, and the before and after pavers pictures should look less shiny but still a good contrast. Include attached logo

```html
<!DOCTYPE html>
<html lang="en">
<head>
<meta charset="utf-8">
<title>Harbor Ridge Painting – Epoxy Flyer</title>
<link href="https://fonts.googleapis.com/css2?family=Barlow+Semi+Condensed:wght@600;700;800&family=Open+Sans:wght@400;600;700&display=swap" rel="stylesheet">
<style>
  :root {
    --navy: #2f3f73;
    --orange: #e38b1f;
    --label-blue: #1f4ea6;
    --label-black: #151515;
    --paper: #ffffff;
    --ink: #1d2340;
    --backdrop: #e6e6e8;
    --concrete-a: #8d8f8c;
    --concrete-b: #5f615f;
    --flake-a: #6f7480;
    --flake-b: #c9ccd2;
    --paver-a: #8a6248;
    --paver-b: #5b3f2e;
    --paver-c: #9a6a48;
    --paver-d: #6a4330;
  }
  * { margin: 0; padding: 0; box-sizing: border-box; }
  html, body { width: 1200px; height: 800px; overflow: hidden; }
  body {
    background: var(--backdrop);
    font-family: "Open Sans", Arial, sans-serif;
    color: var(--ink);
    position: relative;
  }
  .flyer {
    position: absolute;
    left: 300px; top: 12px;
    width: 600px; height: 776px;
    background: var(--paper);
    box-shadow: 0 6px 20px rgba(0,0,0,.18);
    overflow: hidden;
  }
  .photo { position: absolute; }
  .photo--garage-before { left: 20px; top: 20px; width: 146px; height: 310px;
    background: linear-gradient(170deg, #d9d9d6 0%, var(--concrete-a) 30%, var(--concrete-b) 100%); }
  .photo--garage-after { left: 168px; top: 20px; width: 137px; height: 310px;
    background: linear-gradient(170deg, #e3e3e3 0%, var(--flake-b) 25%, var(--flake-a) 100%); }
  .photo--paver-before { left: 310px; top: 20px; width: 270px; height: 155px;
    background: linear-gradient(160deg, #8c7a66 0%, var(--paver-a) 35%, var(--paver-b) 100%); }
  .photo--paver-after { left: 310px; top: 179px; width: 270px; height: 151px;
    background: linear-gradient(160deg, #8a7560 0%, var(--paver-c) 35%, var(--paver-d) 100%); }
  .tag {
    position: absolute;
    font-family: "Barlow Semi Condensed", Arial, sans-serif;
    font-weight: 700; font-size: 17px; line-height: 20px; letter-spacing: .5px;
    color: #fff; padding: 3px 12px;
  }
  .tag--before { background: var(--label-black); }
  .tag--after { background: var(--label-blue); }

  .headline-box {
    position: absolute; left: 20px; top: 330px; width: 285px; height: 110px;
    background: var(--navy); padding: 16px 14px 0 16px;
  }
  .headline {
    font-family: "Barlow Semi Condensed", Arial, sans-serif;
    font-weight: 800; font-size: 25px; line-height: 1.0;
    color: var(--orange); text-transform: uppercase; white-space: nowrap;
  }
  .subhead { color: #fff; font-weight: 600; font-size: 15px; line-height: 1.2; margin-top: 8px; white-space: nowrap; }

  .trust-box {
    position: absolute; left: 310px; top: 330px; width: 270px; height: 212px;
    background: var(--navy); padding: 18px 20px;
  }
  .trust-title {
    font-weight: 700; font-size: 15px; line-height: 1.2; color: var(--orange);
  }
  .trust-list { list-style: none; margin-top: 14px; }
  .trust-item { display: flex; align-items: center; gap: 12px; margin-bottom: 12px; }
  .trust-icon { width: 38px; height: 38px; flex: none; }
  .trust-text { color: #fff; font-size: 12px; font-weight: 600; line-height: 1.25; }

  .services { position: absolute; left: 40px; top: 455px; width: 270px; }
  .service { margin-bottom: 10px; }
  .service-title {
    font-family: "Barlow Semi Condensed", Arial, sans-serif;
    font-weight: 800; font-size: 20px; line-height: 24px; color: var(--navy); text-transform: uppercase;
  }
  .service-list { list-style: none; }
  .service-list li {
    font-size: 12.5px; line-height: 18px; padding-left: 18px; position: relative; white-space: nowrap;
  }
  .service-list li::before {
    content: ""; position: absolute; left: 2px; top: 5px;
    width: 9px; height: 9px; border-radius: 50%; background: var(--navy);
  }

  .brand {
    position: absolute; left: 330px; top: 580px; width: 250px;
    display: flex; align-items: center; gap: 10px;
  }
  .brand-dot { width: 30px; height: 30px; border-radius: 50%; background: var(--orange); flex: none; }
  .brand-name {
    font-weight: 700; font-size: 18px; line-height: 1.15; color: var(--navy);
  }

  .cta { position: absolute; left: 40px; top: 668px; }
  .cta-label {
    font-family: "Barlow Semi Condensed", Arial, sans-serif;
    font-weight: 800; font-size: 20px; line-height: 24px; color: var(--navy); text-transform: uppercase;
  }
  .cta-phone { display: flex; align-items: center; gap: 8px; }
  .cta-phone svg { width: 26px; height: 26px; }
  .cta-number {
    font-family: "Barlow Semi Condensed", Arial, sans-serif;
    font-weight: 800; font-size: 36px; line-height: 1; color: var(--ink);
  }

  .footer-band { position: absolute; left: 0; bottom: 0; width: 600px; height: 130px; }
  .footer-tagline {
    position: absolute; left: 40px; bottom: 7px;
    color: #fff; font-size: 15px; font-weight: 600;
  }
</style>
</head>
<body>
  <main class="flyer">
    <div class="photo photo--garage-before" role="img" aria-label="Worn, cracked concrete garage floor before coating"></div>
    <div class="photo photo--garage-after" role="img" aria-label="Garage floor finished with grey flake epoxy coating"></div>
    <div class="photo photo--paver-before" role="img" aria-label="Faded brick paver driveway before sealing"></div>
    <div class="photo photo--paver-after" role="img" aria-label="Sealed brick paver driveway with restored colour"></div>

    <span class="tag tag--before" style="left:20px; top:304px;">BEFORE</span>
    <span class="tag tag--after" style="left:168px; top:20px;">AFTER</span>
    <span class="tag tag--before" style="left:500px; top:20px;">BEFORE</span>
    <span class="tag tag--after" style="left:500px; top:179px;">AFTER</span>

    <section class="headline-box">
      <h1 class="headline">Upgrade your garage<br>and driveway</h1>
      <p class="subhead">From worn-out to like new</p>
    </section>

    <section class="trust-box">
      <h2 class="trust-title">Practical upgrades that<br>protect &amp; improve your home</h2>
      <ul class="trust-list">
        <li class="trust-item">
          <svg class="trust-icon" viewBox="0 0 38 38" aria-hidden="true">
            <circle cx="19" cy="19" r="18" fill="#fff"/>
            <circle cx="19" cy="19" r="12" fill="var(--orange)"/>
            <path d="M13.5 19.5l4 4 7-8" fill="none" stroke="#fff" stroke-width="2.6" stroke-linecap="round" stroke-linejoin="round"/>
          </svg>
          <span class="trust-text">Licensed<br>and Insured</span>
        </li>
        <li class="trust-item">
          <svg class="trust-icon" viewBox="0 0 38 38" aria-hidden="true">
            <circle cx="19" cy="19" r="18" fill="#fff"/>
            <path d="M11 27L27 11M11 11l16 16" stroke="var(--orange)" stroke-width="3.4" stroke-linecap="round"/>
            <circle cx="27" cy="11" r="3.4" fill="var(--orange)"/>
            <circle cx="11" cy="11" r="3.4" fill="var(--orange)"/>
          </svg>
          <span class="trust-text">Family-Owned<br>Local Business</span>
        </li>
        <li class="trust-item">
          <svg class="trust-icon" viewBox="0 0 38 38" aria-hidden="true">
            <circle cx="19" cy="19" r="18" fill="#fff"/>
            <path d="M19 29s-7-7.5-7-12.5a7 7 0 0 1 14 0C26 21.5 19 29 19 29z" fill="var(--orange)"/>
            <circle cx="19" cy="16.5" r="2.8" fill="#fff"/>
          </svg>
          <span class="trust-text">Serving Prescott and<br>Surrounding Areas</span>
        </li>
      </ul>
    </section>

    <section class="services">
      <div class="service">
        <h3 class="service-title">Epoxy Floor Coatings</h3>
        <ul class="service-list">
          <li>Durable, long-lasting finish</li>
          <li>Slip-resistant texture</li>
          <li>Covers cracks &amp; imperfections</li>
          <li>Easy to clean &amp; maintain</li>
        </ul>
      </div>
      <div class="service">
        <h3 class="service-title">Paver Sealing</h3>
        <ul class="service-list">
          <li>Restores color &amp; enhances appearance</li>
          <li>Protects from sun fading</li>
          <li>Helps prevent weeds &amp; sand loss</li>
          <li>Easier to clean &amp; maintain</li>
        </ul>
      </div>
    </section>

    <svg class="footer-band" viewBox="0 0 600 130" preserveAspectRatio="none" aria-hidden="true">
      <path d="M0 100 L320 100 C400 100 430 60 470 40 C510 20 560 10 600 10 L600 130 L0 130 Z" fill="var(--navy)"/>
    </svg>

    <div class="brand">
      <span class="brand-dot"></span>
      <span class="brand-name">Harbor Ridge Painting</span>
    </div>

    <section class="cta">
      <p class="cta-label">Call for a free estimate</p>
      <div class="cta-phone">
        <svg viewBox="0 0 26 26" aria-hidden="true">
          <path d="M7 3l4 5-2.5 2.5a12 12 0 0 0 7 7L18 15l5 4-2 4C11 24 2 15 3 5z" fill="var(--navy)"/>
        </svg>
        <span class="cta-number">928-555-0147</span>
      </div>
    </section>

    <p class="footer-tagline">Fast, professional service you can trust</p>
  </main>
</body>
</html>
```